Need a Wordpress website for my HVAC company

I need a Wordpress website created for an HVAC company in a competitive market.
Following are some websites I like:
My current website is www.borvicoheating.com - we also have a facebook page with some pictures

We are an airconditioning and heating company that does both residential and commmercial work.
We need the following info on our website:
-mobile friendly
-Schedule an appt -repair/maintnenace/installation (i would like this option to always be on the page even if they scroll down.)
-24 hour service
-coupons /promotions
-financing
-reviews/testimonials
-about
-blog
-Our service area
The following are services we provide:
-Air conditioning - Installation/Service/Maintenance/new construction
-Heating - Installation/Service/Maintenance/new construction ( gas furnace, 2 stage furnace, electric heat)
-Duct - Repair/Replacement/Istallation - (zone systems)
-thermostats (wifi)
-Heat pump
-Air handler
-self communicating systems
-carbon monoxide testing
-hail damage
-duct sealing
-insulation
-Air cleaners - UV Air purifiers
-humidifiers

I would also like Quilbo SEO add on

Target Market(s)

Anyone who needs our services HVAC contractor

Industry/Entity Type

Hvac

Contact Information for Business Card

Phone:480-555-2046
website:www.borvicoheating.com
email pmarsh@borvicoheating.com

Coding

Coded - Design and coding required

Number of Pages Required

5+ page

Font styles to use
Serif
Sans Serif

Requirements
Must have
• I wrote in brief. I already have Webly Nest. Long story I paid for 3 years already. I need someone to put website there. Ive never used Wordpress but would like a template page so I can easily add services.
Nice to have
• Clean, bright, original

```html
<!DOCTYPE html>
<html lang="en">
<head>
<meta charset="utf-8">
<title>Borvico Mechanical Services – Heating &amp; Cooling</title>
<link rel="stylesheet" href="https://fonts.googleapis.com/css2?family=Open+Sans:ital,wght@0,400;0,600;0,700;0,800;1,400&display=swap">
<style>
:root{
  --red:#c8202f;
  --blue:#1e5aa0;
  --blue-dark:#154680;
  --blue-deep:#0f3a6e;
  --nav-top:#2d74c4;
  --nav-bottom:#1a559c;
  --green:#1f8a45;
  --green-dark:#167237;
  --grey-bg:#f1f1f1;
  --text:#555;
  --white:#fff;
}
*{margin:0;padding:0;box-sizing:border-box}
html,body{width:1200px;height:2913px;overflow:hidden}
body{font-family:"Open Sans",Arial,sans-serif;color:var(--text);background:var(--white);position:relative}
.abs{position:absolute}
svg{display:block}

/* header */
.site-header{position:absolute;left:0;top:0;width:1200px;height:150px;background:var(--white)}
.brand{position:absolute;left:80px;top:46px;display:flex;align-items:center;gap:10px}
.brand-mark{width:26px;height:26px;border-radius:50%;background:var(--red)}
.brand-name{font-weight:800;font-size:30px;color:var(--blue);letter-spacing:1px}
.call{position:absolute;left:715px;top:40px}
.call-label{font-weight:700;font-size:15px;color:var(--green)}
.call-number{font-weight:700;font-size:30px;color:var(--red);line-height:34px}
.call-hours{font-weight:700;font-size:12px;color:#777}
.mascot-top{position:absolute;left:968px;top:0;width:162px;height:150px;background:linear-gradient(180deg,#d9e4f2,#8eb0d8);border-radius:0 0 8px 8px}

/* nav */
.main-nav{position:absolute;left:0;top:150px;width:1200px;height:52px;background:linear-gradient(180deg,var(--nav-top),var(--nav-bottom))}
.main-nav ul{list-style:none;display:flex;height:52px;padding-left:75px}
.main-nav li{font-size:14px;font-weight:700;color:var(--white);line-height:52px;padding:0 24px}
.main-nav li.active{background:var(--red);padding:0 36px}

/* hero */
.hero{position:absolute;left:0;top:202px;width:1200px;height:478px;background:linear-gradient(90deg,#ececec,#f5f5f5);overflow:hidden}
.hero-photo{position:absolute;left:540px;top:0;width:660px;height:478px;background:linear-gradient(90deg,rgba(245,245,245,0),#e4e6e8 30%,#d2d6da)}
.hero-title{position:absolute;left:75px;top:118px;width:620px;font-size:28px;line-height:36px;font-weight:800;color:var(--red);text-transform:uppercase}
.appt-title{font-weight:800;color:var(--blue);font-size:37px;text-transform:uppercase;letter-spacing:.5px;white-space:nowrap}
.hero .appt-title{position:absolute;left:75px;top:262px}
.appt-options{position:absolute;display:flex;gap:30px}
.appt-option{display:flex;align-items:center;gap:12px;font-size:14px;font-weight:700;text-transform:uppercase}
.appt-icon{width:62px;height:62px;border-radius:50%;border:2px solid currentColor;display:flex;align-items:center;justify-content:center}
.hero .appt-options{left:75px;top:336px;color:var(--blue)}

/* welcome */
.section-title{font-size:23px;font-weight:700;color:var(--blue);text-align:center;text-transform:uppercase}
.welcome{position:absolute;left:0;top:680px;width:1200px;height:323px}
.welcome .section-title{margin-top:48px}
.welcome p{width:1060px;margin:18px auto 0;text-align:center;font-size:14.5px;line-height:28px}
.btn-outline{display:block;margin:0 auto;width:152px;height:44px;border:2px solid #999;border-radius:2px;text-align:center;line-height:40px;font-size:14px;font-weight:700;color:var(--blue);text-transform:uppercase}
.welcome .btn-outline{margin-top:26px}

/* residential/commercial band */
.split-band{position:absolute;left:0;top:1003px;width:1200px;height:122px;display:flex}
.split-res{width:600px;background:var(--red)}
.split-com{width:600px;background:var(--blue)}
.split-label{position:absolute;top:22px;font-size:34px;line-height:38px;font-weight:800;color:var(--white);text-transform:uppercase;letter-spacing:.5px}
.split-center{position:absolute;left:538px;top:38px;width:124px;height:46px;border-radius:23px;background:var(--white);display:flex;align-items:center;justify-content:center;font-weight:800;font-size:17px;color:var(--blue)}

/* services */
.services{position:absolute;left:0;top:1125px;width:1200px;height:500px}
.services .section-title{margin-top:48px}
.service-cards{position:absolute;left:75px;top:107px;display:flex;gap:27px}
.service-card{width:243px;height:248px;background:linear-gradient(180deg,#f2f2f2,#fafafa);text-align:center;padding-top:36px}
.service-card svg{margin:0 auto}
.service-card h3{margin-top:28px;font-size:16.5px;font-weight:700;color:var(--red);text-transform:uppercase}
.service-card p{margin:6px auto 0;width:190px;font-size:14px;line-height:22px}
.services .btn-outline{position:absolute;left:497px;top:407px;width:208px}

/* testimonials */
.testimonials{position:absolute;left:0;top:1625px;width:1200px;height:270px;background:var(--grey-bg)}
.testimonials .section-title{margin-top:46px}
.quote{width:1060px;margin:20px auto 0;text-align:center;font-style:italic;font-size:14px;line-height:27px}
.quote-author{text-align:center;color:var(--red);font-weight:700;font-size:14px;margin-top:12px}
.slider-arrows{position:absolute;left:582px;top:215px;display:flex;gap:12px}

/* why choose */
.why{position:absolute;left:0;top:1895px;width:1200px;height:398px;background:linear-gradient(100deg,var(--green-dark),var(--green) 55%,#2b9b55)}
.why .section-title{color:var(--white);margin-top:48px}
.why-items{position:absolute;left:75px;top:118px;display:flex}
.why-item{width:270px;text-align:center;color:var(--white)}
.why-item svg{margin:0 auto}
.why-item h3{margin-top:18px;font-size:15px;line-height:20px;font-weight:700;text-transform:uppercase}
.why-item p{margin:6px auto 0;width:186px;font-size:14px;line-height:22px}

/* schedule */
.schedule{position:absolute;left:0;top:2293px;width:1200px;height:260px}
.schedule .appt-title{position:absolute;left:75px;top:36px}
.schedule .appt-options{left:75px;top:112px;color:var(--red)}
.van{position:absolute;left:692px;top:58px;width:436px;height:170px;border-radius:40px 70px 20px 20px;background:linear-gradient(180deg,#e8eef6,#3d6fb3)}

/* footer */
.site-footer{position:absolute;left:0;top:2553px;width:1200px;height:287px;background:var(--blue)}
.footer-col{position:absolute;top:34px;color:var(--white);font-size:13px}
.footer-col h4{font-size:15px;font-weight:700;text-transform:uppercase;margin-bottom:12px}
.footer-col ul{list-style:none}
.footer-col li{line-height:28px}
.contact-line{display:flex;align-items:center;gap:8px;line-height:28px}
.mascot-footer{position:absolute;left:893px;top:36px;width:268px;height:240px;border-radius:8px;background:linear-gradient(180deg,#3b74bb,#2a63a8)}
.bottom-bar{position:absolute;left:0;top:2840px;width:1200px;height:73px;background:var(--blue-deep);color:var(--white)}
.copyright{position:absolute;left:75px;top:26px;font-size:13px}
.social{position:absolute;left:956px;top:24px;display:flex;gap:18px}
.social span{width:20px;height:20px;border-radius:3px;background:var(--white)}
</style>
</head>
<body>

<header class="site-header">
  <div class="brand"><span class="brand-mark"></span><span class="brand-name">BORVICO</span></div>
  <div class="call">
    <div class="call-label">CALL US:</div>
    <div class="call-number">(480) 555-2046</div>
    <div class="call-hours">24 HOURS A DAY - 7 DAYS A WEEK</div>
  </div>
  <div class="mascot-top" role="img" aria-label="Cartoon technician mascot holding a thermometer and giving a thumbs up"></div>
</header>

<nav class="main-nav">
  <ul>
    <li class="active">HOME</li><li>ABOUT US</li><li>24 HOUR SERVICES</li><li>COUPONS</li><li>FINANCING</li><li>REVIEWS</li><li>BLOG</li><li>CONTACT US</li>
  </ul>
</nav>

<section class="hero">
  <div class="hero-photo" role="img" aria-label="Smiling technician giving a thumbs up beside a wall-mounted air conditioner"></div>
  <h1 class="hero-title">We are an air conditioning &amp; heating company that does both residential &amp; commercial work.</h1>
  <h2 class="appt-title">Schedule an appointment</h2>
  <div class="appt-options">
    <div class="appt-option"><span class="appt-icon"><svg width="30" height="30" viewBox="0 0 30 30" fill="none" stroke="currentColor" stroke-width="2.4"><circle cx="15" cy="15" r="5"/><path d="M15 3v5M15 22v5M3 15h5M22 15h5M6.5 6.5l3.5 3.5M20 20l3.5 3.5M6.5 23.5l3.5-3.5M20 10l3.5-3.5"/></svg></span>Repair</div>
    <div class="appt-option"><span class="appt-icon"><svg width="30" height="30" viewBox="0 0 30 30" fill="none" stroke="currentColor" stroke-width="2.6" stroke-linecap="round"><path d="M6 6l18 18M24 6L6 24"/><circle cx="6" cy="6" r="3"/><circle cx="24" cy="24" r="2"/></svg></span>Maintenance</div>
    <div class="appt-option"><span class="appt-icon"><svg width="32" height="30" viewBox="0 0 32 30" fill="none" stroke="currentColor" stroke-width="2.2"><circle cx="11" cy="17" r="7"/><circle cx="11" cy="17" r="2.5"/><circle cx="24" cy="9" r="5"/><circle cx="24" cy="9" r="1.6"/></svg></span>Installation</div>
  </div>
</section>

<section class="welcome">
  <h2 class="section-title">Welcome to our website</h2>
  <p>Aliquam molestie, mi et imperdiet euismod, dui purus auctor tellus, et interdum lacus lectus et ante. Sed accumsan sollicitudin sapien, sit amet adipiscing turpis gravida ac. In congue, neque ac lobortis volutpat, libero mauris varius mi, vitae suscipit ipsum ligula vitae risus. Duis aliquam nibh a dui iaculis viverra id a velit. Vivamus egestas risus in magna varius commodo. Sed semper viverra egestas.<br>Etiam pretium porttitor lectus, vel ornare neque porta volutpat.</p>
  <span class="btn-outline">Read more</span>
</section>

<section class="split-band">
  <div class="split-res"></div><div class="split-com"></div>
  <svg class="abs" style="left:145px;top:28px" width="68" height="66" viewBox="0 0 68 66" fill="#fff"><path d="M34 2L2 28h8v36h48V28h8z"/><rect x="18" y="34" width="9" height="9" fill="#c8202f"/><rect x="41" y="34" width="9" height="9" fill="#c8202f"/><rect x="29" y="46" width="10" height="18" fill="#c8202f"/></svg>
  <div class="split-label" style="left:256px">Residential<br>Services</div>
  <div class="split-center">BORVICO</div>
  <div class="split-label" style="left:716px">Commercial<br>Services</div>
  <svg class="abs" style="left:974px;top:18px" width="100" height="90" viewBox="0 0 100 90" fill="#fff"><path d="M10 90V30l30-10v70z"/><path d="M44 90V8l42 12v70z"/><g fill="#1e5aa0"><rect x="52" y="24" width="7" height="7"/><rect x="66" y="28" width="7" height="7"/><rect x="52" y="40" width="7" height="7"/><rect x="66" y="42" width="7" height="7"/><rect x="52" y="56" width="7" height="7"/><rect x="66" y="56" width="7" height="7"/><rect x="18" y="40" width="6" height="6"/><rect x="18" y="54" width="6" height="6"/><rect x="28" y="40" width="6" height="6"/><rect x="28" y="54" width="6" height="6"/></g></svg>
</section>

<section class="services">
  <h2 class="section-title">Services we offered</h2>
  <div class="service-cards">
    <article class="service-card">
      <svg width="86" height="62" viewBox="0 0 86 62" fill="none" stroke="#c8202f" stroke-width="3"><rect x="4" y="4" width="78" height="26" rx="3" fill="#c8202f"/><rect x="14" y="20" width="58" height="5" fill="#fff" stroke="none"/><path d="M22 38c-4 5 4 9 0 16M36 38c-4 5 4 9 0 16M50 38c-4 5 4 9 0 16M64 38c-4 5 4 9 0 16"/></svg>
      <h3>Air conditioning</h3><p>Aliquam molestie, mi et imperdiet euismod, dui purus auctor..</p>
    </article>
    <article class="service-card">
      <svg width="62" height="62" viewBox="0 0 62 62" fill="none" stroke="#c8202f" stroke-width="3"><path d="M14 4c-3 4 3 7 0 12M31 4c-3 4 3 7 0 12M48 4c-3 4 3 7 0 12"/><rect x="6" y="24" width="50" height="32" rx="4" fill="#c8202f"/><path d="M16 28v24M26 28v24M36 28v24M46 28v24" stroke="#fff"/></svg>
      <h3>Heating</h3><p>Aliquam molestie, mi et imperdiet euismod, dui purus auctor..</p>
    </article>
    <article class="service-card">
      <svg width="76" height="62" viewBox="0 0 76 62" fill="none" stroke="#c8202f" stroke-width="3"><path d="M4 32L38 4l34 28M12 26v32h52V26"/><rect x="22" y="38" width="32" height="12"/><path d="M28 38v12M34 38v12M40 38v12M46 38v12"/></svg>
      <h3>Heat pump</h3><p>Aliquam molestie, mi et imperdiet euismod, dui purus auctor..</p>
    </article>
    <article class="service-card">
      <svg width="44" height="62" viewBox="0 0 44 62" fill="none" stroke="#c8202f" stroke-width="3"><path d="M10 38V8a6 6 0 0112 0v30a11 11 0 11-12 0z"/><circle cx="16" cy="47" r="6" fill="#c8202f"/><path d="M16 22v20M28 12h10M28 20h8M28 28h10"/></svg>
      <h3>Thermostats</h3><p>Aliquam molestie, mi et imperdiet euismod, dui purus auctor..</p>
    </article>
  </div>
  <span class="btn-outline">View all services</span>
</section>

<section class="testimonials">
  <h2 class="section-title">Our customers say</h2>
  <p class="quote">“ Aliquam molestie, mi et imperdiet euismod, dui purus auctor tellus, et interdum lacus lectus et ante. Sed accumsan sollicitudin sapien, sit amet adipiscing turpis gravida ac. In congue, neque ac lobortis volutpat, libero mauris varius mi, vitae suscipit ipsum ligula vitae risus...”</p>
  <p class="quote-author">-Dana R.</p>
  <div class="slider-arrows">
    <svg width="12" height="18" viewBox="0 0 12 18" fill="none" stroke="#555" stroke-width="2.5"><path d="M10 2L3 9l7 7"/></svg>
    <svg width="12" height="18" viewBox="0 0 12 18" fill="none" stroke="#555" stroke-width="2.5"><path d="M2 2l7 7-7 7"/></svg>
  </div>
</section>

<section class="why" role="img" aria-label="Green-tinted background photo of a woman relaxing beside an air conditioning unit">
  <h2 class="section-title">Why choose us</h2>
  <div class="why-items">
    <div class="why-item">
      <svg width="60" height="60" viewBox="0 0 60 60" fill="none" stroke="#fff" stroke-width="3"><circle cx="30" cy="30" r="24"/><text x="30" y="36" text-anchor="middle" fill="#fff" stroke="none" font-family="Open Sans, sans-serif" font-weight="700" font-size="16">24/7</text></svg>
      <h3>24/7 Emergency<br>Service</h3><p>You need air conditioning service when you need it, not when we feel like being open..</p>
    </div>
    <div class="why-item">
      <svg width="60" height="60" viewBox="0 0 60 60" fill="none" stroke="#fff" stroke-width="4.5" stroke-linecap="round"><path d="M10 10l40 40M50 10L10 50"/><circle cx="10" cy="10" r="6" stroke-width="3"/></svg>
      <h3>Same day<br>service</h3><p>You need air conditioning service when you need it, not when we feel like being open..</p>
    </div>
    <div class="why-item">
      <svg width="60" height="60" viewBox="0 0 60 60" fill="none" stroke="#fff" stroke-width="3"><path d="M12 30a18 18 0 0136 0z" fill="#fff"/><path d="M8 32h44M14 54c2-10 8-14 16-14s14 4 16 14"/><path d="M40 44l10 10" stroke-width="4"/></svg>
      <h3>Highly trained<br>technicians</h3><p>You need air conditioning service when you need it, not when we feel like being open..</p>
    </div>
    <div class="why-item">
      <svg width="60" height="60" viewBox="0 0 60 60" fill="none" stroke="#fff" stroke-width="3"><rect x="12" y="8" width="36" height="48" rx="3"/><rect x="22" y="4" width="16" height="8" fill="#fff"/><path d="M18 24l3 3 5-5M30 25h12M18 36l3 3 5-5M30 37h12M18 47h24"/></svg>
      <h3>Free energy<br>survey</h3><p>You need air conditioning service when you need it, not when we feel like being open..</p>
    </div>
  </div>
</section>

<section class="schedule">
  <h2 class="appt-title">Schedule an appointment</h2>
  <div class="appt-options">
    <div class="appt-option"><span class="appt-icon"><svg width="30" height="30" viewBox="0 0 30 30" fill="none" stroke="currentColor" stroke-width="2.4"><circle cx="15" cy="15" r="5"/><path d="M15 3v5M15 22v5M3 15h5M22 15h5M6.5 6.5l3.5 3.5M20 20l3.5 3.5M6.5 23.5l3.5-3.5M20 10l3.5-3.5"/></svg></span>Repair</div>
    <div class="appt-option"><span class="appt-icon"><svg width="30" height="30" viewBox="0 0 30 30" fill="none" stroke="currentColor" stroke-width="2.6" stroke-linecap="round"><path d="M6 6l18 18M24 6L6 24"/><circle cx="6" cy="6" r="3"/><circle cx="24" cy="24" r="2"/></svg></span>Maintenance</div>
    <div class="appt-option"><span class="appt-icon"><svg width="32" height="30" viewBox="0 0 32 30" fill="none" stroke="currentColor" stroke-width="2.2"><circle cx="11" cy="17" r="7"/><circle cx="11" cy="17" r="2.5"/><circle cx="24" cy="9" r="5"/><circle cx="24" cy="9" r="1.6"/></svg></span>Installation</div>
  </div>
  <div class="van" role="img" aria-label="Company service van wrapped in blue and white livery"></div>
</section>

<footer class="site-footer">
  <div class="footer-col" style="left:75px">
    <h4>Company</h4>
    <div style="display:flex;gap:50px">
      <ul><li>Home</li><li>About us</li><li>24 hour Services</li><li>Coupons</li><li>Financing</li></ul>
      <ul><li>Reviews</li><li>Blog</li><li>Contact us</li></ul>
    </div>
  </div>
  <div class="footer-col" style="left:330px">
    <h4>Services</h4>
    <div style="display:flex;gap:28px">
      <ul><li>Air Conditioning</li><li>Heating</li><li>Duct</li><li>Thermostats</li><li>Heat Pump</li><li>Air Handler</li><li>Humidifiers</li></ul>
      <ul><li>Self Communicating Systems</li><li>Carbon Monoxide Testing</li><li>Hail Damage</li><li>Duct Sealing</li><li>Insulation</li><li>Air Cleaners</li></ul>
    </div>
  </div>
  <div class="footer-col" style="left:692px">
    <h4>Contact info</h4>
    <div style="font-weight:700;line-height:28px">COMPANY NAME</div>
    <div class="contact-line" style="align-items:flex-start"><svg width="12" height="16" viewBox="0 0 12 16" fill="#fff" style="margin-top:6px"><path d="M6 0a6 6 0 00-6 6c0 4.5 6 10 6 10s6-5.5 6-10a6 6 0 00-6-6zm0 8.5A2.5 2.5 0 116 3.5a2.5 2.5 0 010 5z"/></svg><span>4120 Larkfield Road<br>Mesa, AZ 85201</span></div>
    <div class="contact-line"><svg width="13" height="13" viewBox="0 0 13 13" fill="#fff"><path d="M3 0l2 3-1.4 1.6a8 8 0 004.8 4.8L10 8l3 2-1 3C5.5 13 0 7.5 0 1z"/></svg>(408) 555-0173</div>
    <div class="contact-line"><svg width="14" height="11" viewBox="0 0 14 11" fill="#fff"><path d="M0 0h14v11H0z"/><path d="M0 0l7 6 7-6" fill="none" stroke="#1e5aa0" stroke-width="1.5"/></svg>info@borvicoheating.com</div>
  </div>
  <div class="mascot-footer" role="img" aria-label="Cartoon technician mascot beside a circular service-with-integrity badge"></div>
</footer>

<div class="bottom-bar">
  <p class="copyright">Copyright © 2016 Borvico Mechanical Services, All Rights Reserved.</p>
  <div class="social"><span></span><span></span><span></span><span></span><span></span></div>
</div>

</body>
</html>
```